Celebrity and Entertainment News Website Needed

Entertainment is one of the favors of Life and I am seeking a standard celebrity website which will discuss in depth news of different celebrities around globe with major focus on American Entertainers. There will be different categories of news from these regions. America, Europe, Asia, Australia and Africa. My website name is quillmarva. Youthful colors should be used for the theme and designs, Users should be able to comment at the bottom of each news. Glossy pictures of well know celebrities should be used. Designers can get knowledge from http://brisktulo.com

```html
<!DOCTYPE html>
<html lang="en">
<head>
<meta charset="utf-8">
<title>Quillmarva — Celebrity News</title>
<link rel="stylesheet" href="https://fonts.googleapis.com/css2?family=Oswald:wght@300;400;500;600&family=Open+Sans:wght@400;600&display=swap">
<style>
:root{
  --navy:#2d4a64;
  --navy-dark:#243d54;
  --blue:#1b8fcc;
  --orange:#f7890f;
  --ink:#33475a;
  --muted:#8a8f94;
  --line:#dcdcdc;
  --page:#f6f6f6;
  --card:#ffffff;
  --footer:#2c2c2c;
  --footer-text:#e6e6e6;
}
*{box-sizing:border-box;margin:0;padding:0}
html,body{width:1200px;height:2808px;overflow:hidden}
body{background:var(--page);font-family:"Open Sans",Arial,sans-serif;color:var(--ink);position:relative}
.abs{position:absolute}
.site-header{left:0;top:0;width:1200px;height:107px;background:var(--navy);border-bottom:4px solid var(--navy-dark)}
.brand{left:75px;top:28px;font-family:"Oswald",sans-serif;font-weight:500;font-size:40px;color:#fff;line-height:48px;letter-spacing:.3px}
.social-top{left:800px;top:20px;display:flex;gap:16px}
.dot{width:16px;height:16px;border-radius:50%;background:#c9d3dc}
.region{left:1040px;top:20px;font-size:13px;color:#e3e9ef;display:flex;align-items:center;gap:6px}
.main-nav{left:560px;top:68px;display:flex;gap:0;font-family:"Oswald",sans-serif;font-size:15px;color:#fff;text-transform:uppercase}
.main-nav span{padding:0 14px}
.search{left:1108px;top:72px}
.lead-title{left:75px;top:146px;width:760px;font-family:"Oswald",sans-serif;font-size:24px;line-height:32px;color:var(--blue)}
.photo{display:block}
.slider-arrow{width:40px;height:40px;border-radius:50%;background:rgba(255,255,255,.75);display:flex;align-items:center;justify-content:center}
.box{background:var(--card);border:1px solid var(--line)}
.box-head{background:var(--orange);color:#fff;font-family:"Oswald",sans-serif;font-size:24px;font-weight:400;padding:0 18px;height:49px;line-height:49px;text-transform:uppercase}
.trending-list{list-style:none;padding:16px 0 0 18px;font-family:"Oswald",sans-serif;font-size:17px;color:var(--ink);text-transform:uppercase}
.trending-list li{height:47px}
.trending-list b{color:var(--orange);font-weight:400;margin-right:4px}
.rule{left:75px;top:638px;width:1048px;height:3px;background:#cfd3d6}
.section-title{font-family:"Oswald",sans-serif;font-size:25px;color:var(--ink);text-transform:uppercase}
.card-body{background:var(--card);padding:0 16px}
.cat{font-family:"Open Sans",sans-serif;font-size:10px;font-weight:600;color:var(--muted);text-transform:uppercase;letter-spacing:.5px}
.headline{font-family:"Oswald",sans-serif;font-weight:300;font-size:22px;line-height:31px;color:var(--ink)}
.news-item{border-bottom:1px solid #e6e6e6;padding:0 0 14px}
.time{font-size:10px;font-weight:600;color:var(--muted);margin-top:8px}
.load-more{left:75px;top:2531px;width:691px;height:52px;text-align:center;line-height:50px;font-family:"Oswald",sans-serif;font-size:19px;color:var(--ink)}
.field{background:#eeeeee;border:1px solid #e1e1e1;height:44px;font-size:12px;color:#777;padding:0 14px;line-height:42px}
.btn{background:var(--navy);color:#fff;font-family:"Oswald",sans-serif;font-size:15px;text-transform:uppercase;text-align:center;line-height:36px;height:36px}
.site-footer{left:0;top:2628px;width:1200px;height:180px;background:var(--footer);color:var(--footer-text);text-align:center}
.footer-links{font-size:13px;margin-top:38px}
.footer-links span{margin:0 8px}
.copyright{font-size:11px;margin-top:14px;color:#cfcfcf}
.social-foot{display:flex;gap:22px;justify-content:center;margin-top:30px}
</style>
</head>
<body>

<header class="site-header abs">
  <div class="brand abs">Quillmarva</div>
  <div class="social-top abs"><i class="dot"></i><i class="dot"></i><i class="dot"></i><i class="dot"></i><i class="dot"></i><i class="dot"></i></div>
  <div class="region abs">
    <svg width="12" height="12" viewBox="0 0 12 12"><circle cx="6" cy="6" r="5.5" fill="#e3e9ef"/></svg>
    America
    <svg width="8" height="6" viewBox="0 0 8 6"><path d="M1 1l3 3 3-3" stroke="#e3e9ef" fill="none" stroke-width="1.4"/></svg>
  </div>
  <nav class="main-nav abs"><span>News</span><span>Style</span><span>TV Scoop</span><span>Red Carpet</span><span>TV Shows</span><span>Events</span><span>More</span></nav>
  <svg class="search abs" width="16" height="16" viewBox="0 0 16 16"><circle cx="6.5" cy="6.5" r="5" stroke="#fff" stroke-width="2" fill="none"/><path d="M10.5 10.5l4 4" stroke="#fff" stroke-width="2.4"/></svg>
</header>

<h1 class="lead-title abs">Vestibulum ante ipsum primis in faucibus orci luctus et ultrices posuere cubilia vel ornare neque porta volutpat.</h1>

<div class="abs" style="left:75px;top:225px;width:780px;height:370px">
  <div class="photo" role="img" aria-label="Actor in a white suit walking past a crowd of press photographers with flashes" style="width:780px;height:370px;background:radial-gradient(ellipse at 50% 30%,#c9ccd0 0%,#7a7f86 45%,#2e3137 100%)"></div>
  <div class="slider-arrow abs" style="left:8px;top:165px"><svg width="14" height="14" viewBox="0 0 14 14"><path d="M9 2L4 7l5 5" stroke="#333" stroke-width="2.4" fill="none"/></svg></div>
  <div class="slider-arrow abs" style="right:8px;top:165px"><svg width="14" height="14" viewBox="0 0 14 14"><path d="M5 2l5 5-5 5" stroke="#333" stroke-width="2.4" fill="none"/></svg></div>
</div>

<aside class="box abs" style="left:885px;top:153px;width:240px;height:442px">
  <div class="box-head">Trending</div>
  <ol class="trending-list">
    <li><b>1.</b>Vivamus egestas</li>
    <li><b>2.</b>Risus in magna</li>
    <li><b>3.</b>Varius commodo sed</li>
    <li><b>4.</b>Semper viverra</li>
    <li><b>5.</b>Egestas</li>
    <li><b>6.</b>Etiam pretium</li>
    <li><b>7.</b>Egestas</li>
    <li><b>8.</b>Etiam pretium</li>
  </ol>
</aside>

<div class="rule abs"></div>

<section class="box abs" style="left:75px;top:665px;width:1048px;height:483px">
  <h2 class="section-title abs" style="left:25px;top:24px">Featured News</h2>
  <svg class="abs" style="left:985px;top:32px" width="36" height="18" viewBox="0 0 36 18"><path d="M12 2L5 9l7 7" stroke="#aaa" stroke-width="3" fill="none"/><path d="M24 2l7 7-7 7" stroke="#333" stroke-width="3" fill="none"/></svg>
</section>

<article class="abs" style="left:101px;top:740px;width:304px">
  <div role="img" aria-label="Actor in a tuxedo holding a gold award statuette" style="height:258px;background:linear-gradient(135deg,#6b5a3a,#1c1c1e 60%,#bfa25a)"></div>
  <div class="card-body" style="height:122px;padding-top:16px"><div class="cat">News</div><div class="headline" style="margin-top:6px">Vestibulum ante ipsum primis in faucibus orci luctus</div></div>
</article>
<article class="abs" style="left:447px;top:740px;width:304px">
  <div role="img" aria-label="Blonde actress in a white gown on the red carpet before photographers" style="height:258px;background:linear-gradient(135deg,#2a2a2c,#6f6f72 55%,#d8d2c8)"></div>
  <div class="card-body" style="height:122px;padding-top:16px"><div class="cat">Red Carpet</div><div class="headline" style="margin-top:6px">Vestibulum ante ipsum primis in faucibus orci luctus</div></div>
</article>
<article class="abs" style="left:794px;top:740px;width:304px">
  <div role="img" aria-label="Singer in a leopard print dress posing in a car" style="height:258px;background:linear-gradient(135deg,#3b3430,#a07a4c 50%,#e4c39a)"></div>
  <div class="card-body" style="height:122px;padding-top:16px"><div class="cat">Shows</div><div class="headline" style="margin-top:6px">Vestibulum ante ipsum primis in faucibus orci luctus</div></div>
</article>

<div class="abs" style="left:75px;top:1180px;width:691px;height:514px">
  <div role="img" aria-label="Video still of a celebrity in sunglasses arriving at a premiere with security and cameras" style="width:691px;height:514px;background:radial-gradient(ellipse at 65% 40%,#7b6f68 0%,#2b2624 55%,#0e0d0d 100%)"></div>
  <svg class="abs" style="left:310px;top:216px" width="72" height="72" viewBox="0 0 72 72"><circle cx="36" cy="36" r="33" fill="none" stroke="#fff" stroke-opacity=".75" stroke-width="5"/><path d="M28 22l22 14-22 14z" fill="#fff" fill-opacity=".8"/></svg>
</div>

<div class="abs" style="left:794px;top:1180px;width:331px">
  <div class="abs" role="img" aria-label="Video still of a group of women in patterned dresses at an event" style="left:0;top:0;width:331px;height:177px;background:linear-gradient(135deg,#3a302a,#9b7a5e 50%,#2a2522)"></div>
  <svg class="abs" style="left:140px;top:64px" width="52" height="52" viewBox="0 0 52 52"><circle cx="26" cy="26" r="23" fill="none" stroke="#fff" stroke-opacity=".75" stroke-width="4"/><path d="M20 15l16 11-16 11z" fill="#fff" fill-opacity=".8"/></svg>
  <div class="cat abs" style="left:0;top:197px">Videos</div>
  <div class="headline abs" style="left:0;top:217px;white-space:nowrap">Suspendisse lobortis turpis in odio</div>
  <div class="abs" role="img" aria-label="Video still of an actor in a tuxedo against a dark background" style="left:0;top:267px;width:331px;height:177px;background:linear-gradient(135deg,#2c2e33,#6b6e74 50%,#1c1d20)"></div>
  <svg class="abs" style="left:140px;top:330px" width="52" height="52" viewBox="0 0 52 52"><circle cx="26" cy="26" r="23" fill="none" stroke="#fff" stroke-opacity=".75" stroke-width="4"/><path d="M20 15l16 11-16 11z" fill="#fff" fill-opacity=".8"/></svg>
  <div class="cat abs" style="left:0;top:463px">Videos</div>
  <div class="headline abs" style="left:0;top:483px;white-space:nowrap">Suspendisse lobortis turpis in odio</div>
</div>

<article class="abs" style="left:75px;top:1724px;width:329px">
  <div role="img" aria-label="Politician speaking and gesturing at a podium" style="height:257px;background:linear-gradient(135deg,#1f2a3d,#5b6273 55%,#a33)"></div>
  <div class="card-body" style="height:121px;padding-top:16px"><div class="cat">TV Scoops</div><div class="headline" style="margin-top:6px">Vestibulum ante ipsum primis in faucibus orci luctus</div></div>
</article>
<article class="abs" style="left:436px;top:1724px;width:330px">
  <div role="img" aria-label="Actor and actress posing together on the red carpet" style="height:257px;background:linear-gradient(135deg,#1e1c1d,#5a4a48 55%,#b89a86)"></div>
  <div class="card-body" style="height:121px;padding-top:16px"><div class="cat">Red Carpet</div><div class="headline" style="margin-top:6px">Vestibulum ante ipsum primis in faucibus orci luctus</div></div>
</article>
<article class="abs" style="left:75px;top:2130px;width:329px">
  <div role="img" aria-label="Blonde actress in a sequined dress being interviewed with microphones" style="height:259px;background:linear-gradient(135deg,#cfc7bc,#8a8074 50%,#3d3833)"></div>
  <div class="card-body" style="height:121px;padding-top:16px"><div class="cat">News</div><div class="headline" style="margin-top:6px">Vestibulum ante ipsum primis in faucibus orci luctus</div></div>
</article>
<article class="abs" style="left:436px;top:2130px;width:330px">
  <div role="img" aria-label="Group of award winners holding gold statuettes" style="height:259px;background:linear-gradient(135deg,#e9e6e0,#7c7f88 45%,#2a3a7a 75%,#d8c46a)"></div>
  <div class="card-body" style="height:121px;padding-top:16px"><div class="cat">Shows</div><div class="headline" style="margin-top:6px">Vestibulum ante ipsum primis in faucibus orci luctus</div></div>
</article>

<div class="load-more box abs">
  <svg width="16" height="16" viewBox="0 0 16 16" style="vertical-align:-2px;margin-right:6px"><g fill="#777"><circle cx="8" cy="2" r="1.6"/><circle cx="13" cy="5" r="1.4"/><circle cx="13" cy="11" r="1.3"/><circle cx="8" cy="14" r="1.2"/><circle cx="3" cy="11" r="1.1"/><circle cx="3" cy="5" r="1"/></g></svg>Load More
</div>

<aside class="box abs" style="left:794px;top:1724px;width:331px;height:642px">
  <div class="box-head">More News</div>
  <div class="abs" style="left:18px;top:70px;width:293px">
    <div class="news-item" style="height:136px"><div class="headline">Vestibulum ante ipsum primis in faucibus orci luctus</div><div class="time">10 hours ago</div></div>
    <div class="news-item" style="height:136px;padding-top:20px"><div class="headline">Vestibulum ante ipsum primis in faucibus orci luctus</div><div class="time">10 hours ago</div></div>
    <div class="news-item" style="height:136px;padding-top:20px"><div class="headline">Vestibulum ante ipsum primis in faucibus orci luctus</div><div class="time">10 hours ago</div></div>
    <div style="padding-top:20px"><div class="headline">Vestibulum ante ipsum primis in faucibus orci luctus</div><div class="time">10 hours ago</div></div>
  </div>
</aside>

<aside class="box abs" style="left:794px;top:2383px;width:331px;height:200px">
  <div class="box-head">Newsletter Sign Up</div>
  <p class="abs" style="left:20px;top:66px;font-size:12px;color:#555">Get daily update directly into your email</p>
  <div class="field abs" style="left:18px;top:96px;width:293px">Enter Email Address</div>
  <div class="btn abs" style="left:190px;top:150px;width:121px">Subscribe</div>
</aside>

<footer class="site-footer abs">
  <div class="footer-links"><span>About Us</span>/<span>FAQ</span>/<span>Careers</span>/<span>Contact Us</span>/<span>Advertise with us</span>/<span>Site Map</span>/<span>Cookie Policy</span></div>
  <div class="copyright">Copyright © 2016. Company Name. All Rihgt Reserved</div>
  <div class="social-foot"><i class="dot"></i><i class="dot"></i><i class="dot"></i><i class="dot"></i><i class="dot"></i><i class="dot"></i></div>
</footer>

</body>
</html>
```